Harbourline Electrical Solutions

On one side. LOGO (underneath:) Commercial Industrial Residential

- NAME & CONTACT DETAILS

Marcus T. Hollings
Project Manager

(Cell icon) (441) 555-0187
(Email icon) hlelectricalsolutions@mailvento.com
(Facebook & Instagram icons )@hlelectricalsolutions

Other side: LOGO - underneath ELECTRICAL CONSTRUCTION & MAINTENANCE . LED LIGHTING & AUTOMATION . LIFE SAFETY SYSTEMS (FIRE ALARM / SECURITY) . DATA & COMMUNICATION

```html
<!DOCTYPE html>
<html lang="en">
<head>
<meta charset="utf-8">
<title>Harbourline Electrical Solutions – Business Card</title>
<link rel="stylesheet" href="https://fonts.googleapis.com/css2?family=Montserrat:wght@500;600;700&family=Nunito+Sans:wght@400;600;700&display=swap">
<style>
  :root {
    --backdrop: #e9e6e2;
    --card-light: #eef0f1;
    --card-light-edge: #dfe3e6;
    --navy-deep: #0f2431;
    --navy-mid: #1b3a4b;
    --swoosh: #1a1a1c;
    --brand-teal: #24495a;
    --ink: #2c3438;
    --gold: #d9c7a6;
    --pale: #d8e0e4;
  }
  * { margin: 0; padding: 0; box-sizing: border-box; }
  html, body { width: 1200px; height: 969px; overflow: hidden; }
  body {
    background: var(--backdrop);
    position: relative;
    font-family: "Nunito Sans", sans-serif;
  }
  .card {
    position: absolute;
    left: 120px; top: 212px;
    width: 960px; height: 547px;
    border-radius: 24px;
    overflow: hidden;
    background: linear-gradient(160deg, var(--card-light) 0%, var(--card-light-edge) 100%);
    box-shadow: 0 10px 30px rgba(0,0,0,.15);
  }
  .card-shapes { position: absolute; inset: 0; width: 100%; height: 100%; }
  .brand {
    position: absolute; left: 47px; top: 72px;
    display: flex; align-items: center; gap: 16px;
  }
  .brand-square { width: 22px; height: 22px; background: var(--brand-teal); }
  .brand-name {
    font-family: "Montserrat", sans-serif; font-weight: 700;
    font-size: 27px; line-height: 1.15; color: var(--brand-teal);
    letter-spacing: .5px; text-transform: uppercase;
  }
  .sectors {
    position: absolute; left: 45px; top: 170px;
    font-family: "Nunito Sans", sans-serif; font-weight: 700;
    font-size: 18px; color: var(--ink); letter-spacing: .2px;
  }
  .sectors .dot { font-size: 12px; margin: 0 6px; vertical-align: 2px; }
  .services {
    position: absolute; left: 45px; top: 228px;
    list-style: none; font-size: 20.5px; color: var(--ink); line-height: 27px;
  }
  .services li::before {
    content: ""; display: inline-block; width: 9px; height: 9px; border-radius: 50%;
    background: var(--navy-mid); margin-right: 14px; vertical-align: 3px;
  }
  .contact {
    position: absolute; right: 45px; top: 312px; text-align: right;
  }
  .person-name {
    font-family: "Montserrat", sans-serif; font-weight: 700;
    font-size: 29px; color: var(--gold); letter-spacing: 1px;
  }
  .person-role { font-size: 19px; color: var(--pale); margin-top: 2px; }
  .contact-list { list-style: none; margin-top: 20px; font-size: 18.5px; color: var(--pale); }
  .contact-list li {
    display: flex; justify-content: flex-end; align-items: center; gap: 14px; height: 27px;
  }
  .contact-icon { width: 18px; height: 18px; flex: none; }
</style>
</head>
<body>
  <div class="card">
    <svg class="card-shapes" viewBox="0 0 918 523" preserveAspectRatio="none" aria-hidden="true">
      <defs>
        <linearGradient id="navyFill" x1="0" y1="0" x2="1" y2="1">
          <stop offset="0" stop-color="#1d3e50"/>
          <stop offset="1" stop-color="#0c1d28"/>
        </linearGradient>
      </defs>
      <path d="M685 0 L918 0 L918 523 L250 523 C420 430 660 250 685 0 Z" fill="url(#navyFill)"/>
      <path d="M640 0 C600 250 430 420 215 518 C450 440 630 270 656 0 Z" fill="var(--swoosh)"/>
    </svg>

    <div class="brand">
      <span class="brand-square"></span>
      <span class="brand-name">Harbourline<br>Electrical Solutions</span>
    </div>
    <p class="sectors">COMMERCIAL<span class="dot">●</span>INDUSTRIAL<span class="dot">●</span>RESIDENTIAL</p>

    <ul class="services">
      <li>Electrical Construction &amp; Maintenance</li>
      <li>LED Lighting &amp; Automation</li>
      <li>Life Safety Systems(Fire Alarm / Security)</li>
      <li>Data &amp; Communication</li>
    </ul>

    <div class="contact">
      <p class="person-name">MARCUS T. HOLLINGS</p>
      <p class="person-role">Project Manager</p>
      <ul class="contact-list">
        <li>(441) 555-0187
          <svg class="contact-icon" viewBox="0 0 18 18"><rect x="5" y="1" width="8" height="16" rx="1.5" fill="none" stroke="var(--pale)" stroke-width="1.6"/><circle cx="9" cy="14" r="1" fill="var(--pale)"/></svg>
        </li>
        <li>hlelectricalsolutions@mailvento.com
          <svg class="contact-icon" viewBox="0 0 18 18"><rect x="2" y="5" width="14" height="9" fill="var(--pale)"/><path d="M2 5 L9 10 L16 5" fill="none" stroke="var(--navy-deep)" stroke-width="1.3"/></svg>
        </li>
        <li>@hlelectricalsolutions
          <svg class="contact-icon" viewBox="0 0 18 18"><circle cx="9" cy="9" r="8" fill="var(--pale)"/></svg>
        </li>
        <li>@hlelectricalsolutions
          <svg class="contact-icon" viewBox="0 0 18 18"><circle cx="9" cy="9" r="8" fill="var(--pale)"/></svg>
        </li>
      </ul>
    </div>
  </div>
</body>
</html>
```